Under Morning Lantern website

I need a website to sell my t-shirt designs. I have around 5 designs I plan to sell on my initial launch, but only 3 photos at the moment. I would love a main page with the product images below maybe a large nicely designed header image, showing products with their sizes, item name/description, a way to add to cart and a review system like stars below each product image. Maybe a share option to Snapwall, Facepage, Chirper, Pinterest, etc. would be cool too. Also on the main page under the product images a section showcasing my Snapwall photos for the company. Then a section where I will include an About Me video from like YouTube. Lastly, on the main page an option to join my Mailing List at the footer with links to my Facepage and Snapwall social accounts, links to pages (About Me, Shop, Snapwall page, & Contact Us) as well as Track Order.

The other 4 pages will be for an About Me, which is the video I will make later that will be from YouTube. Then the Shop page. Then the Snapwall page showcasing all the photos I plan to use to market the products, and a Contact Us Page.

I plan to possibly connect this to Shopify, so showcasing payment options (Palo, Birch Pay, Wayfarer, etc.) would be nice.

Lastly, I don't plan on doing returns/exchanges so maybe an area showing that would be nice too. ALL SALES FINAL

Mobile Friendly!

1st image is logo and other 4 images are t-shirt designs

Coded - Design and coding required

5+ page

• Separate pages, No Refunds (All Sales Final), Add to Cart, Way to Purchase

```html
<!DOCTYPE html>
<html lang="en">
<head>
<meta charset="utf-8">
<title>Under Morning Lantern — Shop</title>
<link href="https://fonts.googleapis.com/css2?family=Poppins:wght@300;400;500;600;700&display=swap" rel="stylesheet">
<style>
:root{
  --blue:#00a8ec;
  --grey:#d0d5dc;
  --ink:#2b2b2b;
  --muted:#9a9a9a;
  --line:#e3e3e3;
  --lilac:#dcc8f3;
  --lilac-deep:#cfb6ef;
  --purple:#6b3fa6;
  --purple-soft:#7b52b9;
  --teal:#2fb9b0;
  --footer:#2d2d2d;
  --card-hover:#eef8fd;
}
*{box-sizing:border-box;margin:0;padding:0}
html,body{width:1200px;height:3433px;overflow:hidden}
body{position:relative;font-family:'Poppins',sans-serif;color:var(--ink);background:#fff}
.abs{position:absolute}

/* hero */
.hero{left:0;top:0;width:1200px;height:676px;background:var(--grey)}
.hero-blue{left:0;top:0;width:600px;height:676px;background:var(--blue)}
.brand{font-weight:700;font-size:46px;letter-spacing:1px;color:#000;line-height:1}
.brand-sub{font-size:9px;font-weight:600;letter-spacing:3px;color:#fff}
.nav{left:428px;top:48px;width:343px;height:40px;background:#fff;border-radius:20px;display:flex;align-items:center;justify-content:space-around;padding:0 18px;font-size:13px;color:#666}
.nav .active{color:#222;position:relative}
.nav .active::after{content:"";position:absolute;left:50%;bottom:-7px;width:3px;height:3px;border-radius:50%;background:#222}
.track{left:953px;top:58px;font-size:14px;color:#555}
.cart-badge{left:1066px;top:48px;width:16px;height:16px;border-radius:50%;background:var(--blue);color:#fff;font-size:10px;text-align:center;line-height:16px}
.hero-label{font-size:16px;color:#fff;line-height:21px}
.rule{height:1px}
.btn-outline{border:2px solid #fff;border-radius:20px;color:#fff;font-size:14px;font-weight:500;text-align:center}
.hero-shirt{left:427px;top:157px;width:330px;height:360px;background:#111;border-radius:40px 40px 10px 10px}
.hero-title{left:300px;top:322px;width:600px;text-align:center;font-size:100px;font-weight:700;color:#fff;line-height:1;letter-spacing:-1px}
.hero-sub{left:300px;top:428px;width:600px;text-align:center;font-size:20px;color:#fff}
.size-dot{width:30px;height:30px;border:2px solid #fff;border-radius:50%;color:#fff;font-size:11px;text-align:center;line-height:26px}
.size-dot.on{background:#fff;color:var(--blue)}
.arrow-btn{width:37px;height:37px;display:flex;align-items:center;justify-content:center}

/* tabs */
.tab{top:750px;font-size:29px;color:var(--muted)}
.tab.on{color:var(--ink)}

/* products */
.card{width:220px;height:323px;border:1px solid var(--line);background:#fff}
.card.hover{background:var(--card-hover);border-color:#59c6f0}
.card .shot{position:absolute;left:30px;top:30px;width:160px;height:170px;border-radius:14px}
.card .name{position:absolute;left:35px;top:222px;font-size:16px;font-weight:600}
.card .type{position:absolute;left:35px;top:244px;font-size:16px;color:#555}
.card .price{position:absolute;left:35px;top:270px;font-size:17px;font-weight:700}
.card .tool{position:absolute;left:163px;width:40px;height:40px;border-radius:50%;border:1.5px solid var(--blue);background:#fff;display:flex;align-items:center;justify-content:center}
.card .tool.fill{background:var(--blue)}
.btn-pill{background:var(--blue);color:#fff;border-radius:20px;font-size:14px;font-weight:500;display:flex;align-items:center;justify-content:center;gap:10px}

/* promo */
.promo{left:0;top:1669px;width:1200px;height:427px;background:var(--lilac);overflow:hidden}
.promo-copy{left:560px;width:434px;text-align:center}

/* snapwall */
.gallery-tile{border-radius:0}

/* video */
.band{background:var(--blue)}
.video{left:353px;top:2655px;width:492px;height:276px;background:linear-gradient(135deg,#6d5a88 0%,#4a7f78 60%,#3a6a5f 100%)}
.video-bar{left:0;bottom:0;width:492px;height:35px;background:#111}

/* footer */
.footer{left:0;top:3189px;width:1200px;height:244px;background:var(--footer)}
.foot-head{color:#fff;font-size:15px}
.foot-text{color:#a5a5a5;font-size:13px}
.foot-div{width:1px;background:#444}
</style>
</head>
<body>

<!-- HERO -->
<section class="abs hero"></section>
<div class="abs hero-blue"></div>

<div class="abs" style="left:117px;top:40px">
  <div class="brand">U.M.L.</div>
  <div class="brand-sub" style="margin-top:6px">UNDER MORNING LANTERN</div>
</div>

<nav class="abs nav">
  <span class="active">About</span><span>Shop</span><span>Snapwall</span><span>Contact</span>
</nav>

<div class="abs track">Track Order</div>
<svg class="abs" style="left:1050px;top:56px" width="26" height="24" viewBox="0 0 26 24" fill="none" stroke="#666" stroke-width="1.6">
  <path d="M1 2h4l3 13h13l3-9H7"/><circle cx="10" cy="20" r="2"/><circle cx="19" cy="20" r="2"/>
</svg>
<div class="abs cart-badge">0</div>

<div class="abs rule" style="left:117px;top:280px;width:43px;background:#fff"></div>
<div class="abs hero-label" style="left:175px;top:270px">Product<br>Item Name</div>
<div class="abs btn-outline" style="left:117px;top:362px;width:139px;height:38px;line-height:34px">Shop Now</div>

<div class="abs hero-shirt" role="img" aria-label="Black half sleeve t-shirt with the lantern graphic"></div>
<div class="abs hero-title">Colorblack</div>
<div class="abs hero-sub">Half sleeve t-shirt</div>

<div class="abs" style="left:933px;top:268px;font-size:16px;color:#444">Color : Black</div>
<div class="abs rule" style="left:1040px;top:280px;width:43px;background:#666"></div>

<div class="abs" style="left:116px;top:588px;font-size:14px;font-weight:600;color:#fff">Size:</div>
<div class="abs rule" style="left:158px;top:598px;width:27px;background:#fff"></div>
<div class="abs size-dot" style="left:200px;top:582px">S</div>
<div class="abs size-dot on" style="left:236px;top:582px">M</div>
<div class="abs size-dot" style="left:271px;top:582px">L</div>
<div class="abs size-dot" style="left:306px;top:582px">XL</div>

<div class="abs arrow-btn" style="left:996px;top:579px;background:var(--blue)">
  <svg width="10" height="12" viewBox="0 0 10 12"><path d="M7 1 2 6l5 5" stroke="#fff" stroke-width="2" fill="none"/></svg>
</div>
<div class="abs arrow-btn" style="left:1045px;top:579px;background:#b9c0ca">
  <svg width="10" height="12" viewBox="0 0 10 12"><path d="M3 1l5 5-5 5" stroke="#fff" stroke-width="2" fill="none"/></svg>
</div>

<!-- TABS -->
<div class="abs tab on" style="left:327px">New Arrival</div>
<div class="abs" style="left:324px;top:789px;width:169px;height:2px;background:var(--ink)"></div>
<div class="abs tab" style="left:547px">Sale Off</div>
<div class="abs tab" style="left:718px">Best Selling</div>

<!-- PRODUCTS -->
<div class="abs card" style="left:120px;top:841px"><div class="shot" role="img" aria-label="Black t-shirt with blue lettering" style="background:#151515"></div><div class="name">Product Name</div><div class="type">T-shirt</div><div class="price">$120.00</div></div>

<div class="abs card hover" style="left:367px;top:841px">
  <div class="shot" role="img" aria-label="Black t-shirt with blue logo print" style="background:#151515;width:140px"></div>
  <div class="tool" style="top:23px"><svg width="16" height="16" viewBox="0 0 16 16" fill="none" stroke="#555" stroke-width="1.3"><path d="M2 6V2h4M14 6V2h-4M2 10v4h4M14 10v4h-4M2 2l12 12M14 2 2 14"/></svg></div>
  <div class="tool" style="top:77px"><svg width="16" height="14" viewBox="0 0 16 14" fill="none" stroke="#555" stroke-width="1.3"><path d="M8 13 2 7a3.5 3.5 0 0 1 6-4 3.5 3.5 0 0 1 6 4z"/></svg></div>
  <div class="tool fill" style="top:132px"><svg width="16" height="14" viewBox="0 0 16 14" fill="none" stroke="#fff" stroke-width="1.5"><path d="M1 1h3l2 8h7l2-6H5"/><circle cx="7" cy="12" r="1"/><circle cx="12" cy="12" r="1"/></svg></div>
  <div class="name">Product Name</div><div class="type">T-shirt</div><div class="price">$120.00</div>
</div>

<div class="abs card" style="left:613px;top:841px"><div class="shot" role="img" aria-label="Two white t-shirts with yellow heart print" style="background:#e4e4e4"></div><div class="name">Product Name</div><div class="type">T-shirt</div><div class="price">$120.00</div></div>
<div class="abs card" style="left:860px;top:841px"><div class="shot" role="img" aria-label="Black t-shirt with purple logo print" style="background:#151515"></div><div class="name">Product Name</div><div class="type">T-shirt</div><div class="price">$120.00</div></div>

<div class="abs card" style="left:120px;top:1191px"><div class="shot" role="img" aria-label="Black and white t-shirts pair" style="background:linear-gradient(90deg,#151515 50%,#e0e0e0 50%)"></div><div class="name">Product Name</div><div class="type">T-shirt</div><div class="price">$120.00</div></div>
<div class="abs card" style="left:367px;top:1191px"><div class="shot" role="img" aria-label="Teal t-shirt with black lettering" style="background:var(--teal)"></div><div class="name">Product Name</div><div class="type">T-shirt</div><div class="price">$120.00</div></div>
<div class="abs card" style="left:613px;top:1191px"><div class="shot" role="img" aria-label="Black and purple t-shirts pair" style="background:linear-gradient(90deg,#151515 45%,#8c5cc8 45%)"></div><div class="name">Product Name</div><div class="type">T-shirt</div><div class="price">$120.00</div></div>
<div class="abs card" style="left:860px;top:1191px"><div class="shot" role="img" aria-label="Black t-shirt with blue logo print" style="background:#151515"></div><div class="name">Product Name</div><div class="type">T-shirt</div><div class="price">$120.00</div></div>

<div class="abs btn-pill" style="left:543px;top:1553px;width:114px;height:39px">More
  <svg width="7" height="11" viewBox="0 0 7 11"><path d="M1 1l4.5 4.5L1 10" stroke="#fff" stroke-width="1.8" fill="none"/></svg>
</div>

<!-- PROMO -->
<section class="abs promo">
  <svg class="abs" style="left:0;top:0" width="1200" height="427" viewBox="0 0 1200 427">
    <path d="M0 180C300 130 520 330 780 320C960 313 1080 260 1200 250V427H0Z" fill="var(--lilac-deep)"/>
  </svg>
  <div class="abs" role="img" aria-label="Purple and teal t-shirts layered" style="left:184px;top:71px;width:320px;height:293px;border-radius:30px;background:linear-gradient(120deg,#8c5cc8 0%,#8c5cc8 50%,var(--teal) 50%,var(--teal) 100%)"></div>
  <div class="abs promo-copy" style="top:78px;font-size:26px;font-weight:500;color:var(--purple-soft)">New Arrival</div>
  <div class="abs promo-copy" style="top:124px;font-size:86px;font-weight:700;color:var(--purple);line-height:1.1">Sale 20%</div>
  <div class="abs promo-copy" style="top:234px;font-size:28px;font-weight:500;color:var(--purple-soft)">Only $99.00</div>
  <div class="abs" style="left:707px;top:307px;width:140px;height:40px;border-radius:20px;background:var(--purple);color:#fff;font-size:14px;font-weight:500;text-align:center;line-height:40px">Shop Now</div>
</section>

<!-- SNAPWALL -->
<h2 class="abs" style="left:272px;top:2152px;font-size:30px;font-weight:700">Snapwall</h2>
<p class="abs" style="left:272px;top:2197px;width:680px;font-size:16px;line-height:21px">Meet your fellow Humans! Show us your Lantern style on Chirper, Snapwall or Facepage and tag @UML for a chance to win free tees and be featured on our site!</p>

<div class="abs gallery-tile" style="left:255px;top:2269px;width:317px;height:294px;background:#3b3f47">
  <div class="abs" role="img" aria-label="Purple t-shirt feature image" style="left:70px;top:50px;width:177px;height:200px;border-radius:20px;background:#8c5cc8"></div>
</div>
<div class="abs gallery-tile" role="img" aria-label="Customer photo outdoors by rocks" style="left:585px;top:2269px;width:178px;height:142px;background:linear-gradient(160deg,#7fa8c9,#7d6f63)"></div>
<div class="abs gallery-tile" role="img" aria-label="Customer in black hoodie in a field" style="left:775px;top:2269px;width:170px;height:142px;background:linear-gradient(180deg,#c9d1d6,#8a8576)"></div>
<div class="abs gallery-tile" role="img" aria-label="Customer in white t-shirt against a wall" style="left:585px;top:2423px;width:178px;height:140px;background:linear-gradient(160deg,#5f6466,#9a9c9a)"></div>
<div class="abs gallery-tile" role="img" aria-label="Customer seated on a city boardwalk" style="left:775px;top:2423px;width:170px;height:140px;background:linear-gradient(180deg,#b7c4cc,#7f7a72)"></div>

<!-- ABOUT / VIDEO -->
<div class="abs band" style="left:0;top:2713px;width:339px;height:163px"></div>
<div class="abs band" style="left:860px;top:2713px;width:340px;height:163px"></div>
<div class="abs" style="left:117px;top:2752px;font-size:30px;color:#fff;font-weight:300">About <b style="font-weight:700">Me</b></div>
<div class="abs" style="left:117px;top:2801px;font-size:16px;color:#fff">Check out the video</div>
<div class="abs btn-outline" style="left:944px;top:2776px;width:139px;height:39px;line-height:35px">Shop Now</div>

<div class="abs video" role="img" aria-label="About me video still with purple and teal t-shirts">
  <div class="abs" style="left:30px;top:20px;font-size:16px;color:#ddd">U.M.L. &nbsp; About UML Check out the video</div>
  <svg class="abs" style="left:216px;top:90px" width="60" height="60" viewBox="0 0 60 60">
    <circle cx="30" cy="30" r="30" fill="rgba(255,255,255,.35)"/><path d="M24 18v24l19-12z" fill="#fff"/>
  </svg>
  <div class="abs video-bar">
    <svg class="abs" style="left:14px;top:12px" width="9" height="11" viewBox="0 0 9 11"><path d="M0 0v11l9-5.5z" fill="#fff"/></svg>
    <div class="abs" style="left:37px;top:16px;width:310px;height:3px;background:#555"></div>
    <div class="abs" style="left:37px;top:16px;width:117px;height:3px;background:#ddd"></div>
    <div class="abs" style="left:357px;top:9px;font-size:10px;color:#ddd">03:47 / 10:00</div>
    <svg class="abs" style="left:432px;top:12px" width="12" height="11" viewBox="0 0 12 11"><path d="M0 3h3l4-3v11L3 8H0z" fill="#ddd"/><path d="M9 3q2 2.5 0 5" stroke="#ddd" fill="none"/></svg>
    <div class="abs" style="left:460px;top:9px;font-size:10px;font-weight:700;color:var(--blue)">HD</div>
  </div>
</div>

<!-- NEWSLETTER -->
<h2 class="abs" style="left:0;top:2994px;width:1200px;text-align:center;font-size:34px;font-weight:400">Join Our Newsletter</h2>
<p class="abs" style="left:0;top:3044px;width:1200px;text-align:center;font-size:12px;color:#777">Sale up to 20% off for your next purchase in this month!</p>
<div class="abs" style="left:261px;top:3094px;font-size:10px;color:#bbb">Your email address</div>
<div class="abs" style="left:888px;top:3094px;font-size:10px;color:#bbb">Subscribe</div>
<div class="abs" style="left:261px;top:3119px;width:678px;height:1px;background:#ccc"></div>

<!-- FOOTER -->
<footer class="abs footer">
  <div class="abs foot-head" style="left:153px;top:42px">Contact Us</div>
  <div class="abs foot-text" style="left:153px;top:82px;line-height:21px">Lorem Ipsum, is simply<br>dummy text of the</div>
  <div class="abs foot-text" style="left:153px;top:137px">+000 0000 00000</div>
  <div class="abs foot-text" style="left:153px;top:168px">hello@morninglantern.shop</div>
  <div class="abs foot-div" style="left:403px;top:44px;height:180px"></div>

  <div class="abs foot-head" style="left:529px;top:42px">Contact Us</div>
  <div class="abs foot-text" style="left:529px;top:84px;line-height:26.5px">Home<br>About<br>Services<br>Contact</div>
  <div class="abs foot-div" style="left:733px;top:44px;height:180px"></div>

  <div class="abs" style="left:837px;top:66px;width:200px;text-align:center">
    <div style="font-size:34px;font-weight:700;color:var(--blue);line-height:1">U.M.L.</div>
    <div style="font-size:7px;font-weight:600;letter-spacing:2.5px;color:#fff;margin-top:5px">UNDER MORNING LANTERN</div>
  </div>
  <svg class="abs" style="left:870px;top:143px" width="136" height="14" viewBox="0 0 136 14" fill="#bbb">
    <circle cx="7" cy="7" r="6"/><circle cx="38" cy="7" r="6"/><circle cx="68" cy="7" r="6"/><circle cx="98" cy="7" r="6"/><circle cx="128" cy="7" r="6"/>
  </svg>
</footer>

</body>
</html>
```